Chorefinch clone for Asia

I am developing a clone for www.chorefinchly.example. It is meant for Asia (i.e. Singapore, Australia, Indonesian, Philippines, Malaysia).

I need a webdesign that functionally look like chorefinch, but localised with pictures of Asian of multi country (rather than latin american looks).

The color, iconography, images can be different, but the functionality must be all be similar to www.chorefinchly.example

I need a mobile UI as well that is for a mobile app, again, similar to that of chorefinch mobile app.

Note that I need the design for the following pages:
1. homepage
2. login page
3. page after login in.
4. search page & results
5. post a task & confirmation page
6. Payment page
7. User Review page.
8. Sign up page.

The webpages are to be in english....

The features must have photos of friendly looking helpers.

Bullseye Mart Market(s)

Asian countries. To serve a mass market, for part time, one off task job.

Requirements
Must have
• Just use ChoreFinchAsia for the name of the site for Starters. I have not arrived at a name yet.

```html
<!DOCTYPE html>
<html lang="en">
<head>
<meta charset="utf-8">
<title>Mira Lane – Delivery</title>
<link href="https://fonts.googleapis.com/css2?family=PT+Sans:wght@400;700&display=swap" rel="stylesheet">
<style>
:root{
  --teal:#3f9fa3;
  --teal-dark:#2f8588;
  --teal-light:#7cc3c5;
  --head-bg:#d7e6e9;
  --panel:#eef4f5;
  --line:#d3dfe2;
  --orange:#f39a12;
  --orange-dark:#e07d00;
  --price:#e8701e;
  --wine:#8d1f1f;
  --blue:#3d86c6;
  --text:#3b4a50;
  --muted:#8a9aa0;
  --foot:#d6e4e7;
  --foot-dark:#c5d6da;
  --link:#2f6fae;
}
*{box-sizing:border-box;margin:0;padding:0}
html,body{width:787px;height:1200px;overflow:hidden}
body{font-family:"PT Sans",Arial,sans-serif;color:var(--text);background:#fff}
.page{position:relative;width:787px;height:1200px;overflow:hidden;background:#fff}
ul{list-style:none}
.abs{position:absolute}

/* header */
.site-header{position:absolute;left:0;top:0;width:787px;height:101px;background:linear-gradient(#e3eef0,#d3e3e6);border-top:8px solid var(--teal);border-bottom:1px solid #c4d6da}
.main-nav{position:absolute;left:416px;top:2px;width:339px;height:30px;background:linear-gradient(var(--teal-light),var(--teal));border-radius:0 0 8px 14px;display:flex;justify-content:space-between;padding-right:10px;white-space:nowrap}
.main-nav a{color:#fff;font-size:12px;text-decoration:none;line-height:26px;padding:0 6px;white-space:nowrap}
.main-nav a.active{background:rgba(255,255,255,.22);border-radius:0 0 0 12px;padding:0 15px}
.brand{position:absolute;left:34px;top:33px;display:flex;align-items:center;gap:8px}
.brand-mark{width:34px;height:34px;border-radius:50%;background:var(--teal)}
.brand-name{font-size:37px;color:var(--teal);font-weight:400;line-height:40px;white-space:nowrap}
.social-btn{position:absolute;top:50px;height:19px;border-radius:2px;color:#fff;font-size:8px;font-weight:700;display:flex;align-items:center;padding-left:5px;gap:5px;white-space:nowrap;overflow:hidden}
.social-btn i{display:block;flex:none;width:12px;height:12px;background:rgba(255,255,255,.35);border-radius:2px}
.social-btn.chirper{left:416px;width:98px;background:linear-gradient(#4fb5e6,#2a8fc6)}
.social-btn.friendbook{left:526px;width:104px;background:linear-gradient(#5b7bb5,#3b5a98)}
.search{position:absolute;left:643px;top:49px;width:111px;height:19px;background:#fff;border:1px solid #c7d5d9;border-radius:2px;font-size:9px;font-style:italic;color:#a9b4b8;padding:3px 8px}
.search svg{position:absolute;right:5px;top:4px}

/* category panel */
.category{position:absolute;left:34px;top:103px;width:721px;height:94px;background:#fff;border-radius:0 0 8px 8px;box-shadow:0 1px 3px rgba(0,0,0,.06)}
.category h1{position:absolute;left:17px;top:15px;font-size:18px;font-weight:400;color:var(--wine)}
.category .rule{position:absolute;left:17px;top:42px;width:690px;border-top:1px solid #e1e8ea}
.more-cats{position:absolute;left:594px;top:16px;width:111px;height:17px;border:1px solid #c7d2d5;border-radius:2px;font-size:9px;font-style:italic;color:#6c7a80;padding:2px 11px;background:linear-gradient(#fff,#f1f4f5);white-space:nowrap}
.more-cats::after{content:"";position:absolute;right:8px;top:6px;border:4px solid transparent;border-top-color:#8a979c}
.subnav{position:absolute;left:22px;top:66px;display:flex;font-size:10px;white-space:nowrap}
.subnav li{padding-left:10px;position:relative;margin-right:25px}
.subnav li::before{content:"";position:absolute;left:1px;top:5px;width:3px;height:3px;border-radius:50%;background:#7a868b}
.subnav li.other::after{content:"";display:inline-block;margin-left:5px;border:4px solid transparent;border-top-color:#8a979c;vertical-align:-3px}
.post-task{position:absolute;left:594px;top:51px;width:111px;height:32px;background:linear-gradient(#ffb233,var(--orange-dark));border-radius:4px;color:#fff;font-size:14px;font-weight:700;text-align:center;line-height:31px;box-shadow:0 2px 2px rgba(0,0,0,.15);letter-spacing:.3px;white-space:nowrap}

/* task list */
.recent{position:absolute;left:51px;top:214px;width:427px}
.recent h2{font-size:16px;font-weight:400;color:var(--price);padding-bottom:5px;border-bottom:1px dashed #b9c4c7}
.task{position:absolute;left:0;width:427px;height:113px}
.avatar{position:absolute;left:2px;top:0;width:38px;height:39px;border:1px solid #6aa9ac;background:linear-gradient(#5a6a70,#2e3a40)}
.level{position:absolute;left:2px;top:47px;font-size:8.5px;color:var(--muted);white-space:nowrap}
.task h3{position:absolute;left:51px;top:-2px;font-size:12px;font-weight:400;color:#e0860c;white-space:nowrap}
.task p{position:absolute;left:51px;top:16px;width:376px;font-size:8.6px;line-height:12.5px;color:var(--muted)}
.task-bar{position:absolute;left:0;top:68px;width:427px;height:28px;background:var(--panel);border-radius:3px;font-size:10.5px;display:flex;align-items:center;padding-left:10px;white-space:nowrap}
.task-bar .price{color:var(--price);margin-left:5px}
.task-bar .rating{position:absolute;left:180px;display:flex;align-items:center;gap:5px}
.use-template{position:absolute;right:8px;top:4px;width:84px;height:19px;background:linear-gradient(#ffb233,var(--orange-dark));border-radius:3px;color:#fff;font-size:9px;font-weight:700;text-align:center;line-height:19px}

.pager{position:absolute;left:198px;top:937px;display:flex;gap:2px;font-size:7.5px;white-space:nowrap}
.pager span{border:1px solid #b8cdd2;color:#5a7f8a;height:14px;line-height:12px;padding:0 3px;min-width:13px;text-align:center}
.pager span.on{background:var(--teal);color:#fff;border-color:var(--teal)}
.pager span.gap{border:0}
.pager span.next{color:var(--link);font-weight:700}

/* sidebar */
.widget{position:absolute;left:519px;width:221px;background:#e6eff1;border-radius:8px;overflow:hidden}
.widget h2{height:31px;background:linear-gradient(var(--teal-light),var(--teal));color:#fff;font-size:14.5px;font-weight:400;padding:6px 15px;border-radius:8px 8px 0 0;white-space:nowrap}
.price-widget{top:210px;height:267px}
.price-widget .sub{text-align:center;font-size:10px;font-weight:700;color:#4c5a60;margin:9px 0 0;padding-bottom:10px;border-bottom:1px solid #d5e0e3}
.price-row{position:absolute;left:15px;display:flex;align-items:center;width:192px}
.price-row b{width:31px;font-size:14px;color:var(--blue)}
.track{width:161px;height:7px;border-radius:4px;background:#a6acaf;overflow:hidden}
.track i{display:block;height:100%;background:var(--orange)}
.city-widget{top:489px;height:238px}
.city-list{position:absolute;left:13px;top:44px;display:grid;grid-template-columns:59px 79px 70px;row-gap:6px;font-size:8.8px;white-space:nowrap}
.city-list li{padding-left:9px;position:relative}
.city-list li::before,.arrow-list li::before{content:"";position:absolute;left:0;top:3px;border:3px solid transparent;border-left:4px solid #5e6a6f}
.map{position:absolute;left:14px;top:102px;width:193px;height:120px;border-radius:6px;border:3px solid #fff;background:linear-gradient(135deg,#e8e5dc,#d9d6cc 50%,#e9e3b7)}

/* popular */
.popular{position:absolute;left:34px;top:959px;width:721px;border-top:1px solid #ccd7da}
.popular-col{position:absolute;top:15px;white-space:nowrap}
.popular-col h3{font-size:12px;font-weight:400;color:#333;margin-bottom:6px}
.arrow-list li{position:relative;padding-left:10px;font-size:9.5px;line-height:17.3px;white-space:nowrap}
.arrow-list li::before{top:6px;border-width:3px;border-left-width:4px}
.popular .arrow-list li::before{border-left-color:#555}

/* footer */
.site-footer{position:absolute;left:0;top:1070px;width:787px;height:87px;background:var(--foot)}
.foot-col{position:absolute;top:13px;white-space:nowrap}
.foot-col h4{font-size:9.5px;font-weight:400;color:var(--link);margin-bottom:6px}
.foot-col .arrow-list li{font-size:8.8px;line-height:16.3px}
.cards{display:flex;gap:5px;margin-top:3px}
.cards i{display:block;width:22px;height:15px;border-radius:2px;border:1px solid #b8c6ca;background:#fff}
.cards i:nth-child(5){background:#233f8f}
.call{font-size:9.5px;font-weight:700;color:var(--link);margin-top:15px}
.bottom-bar{position:absolute;left:0;top:1157px;width:787px;height:43px;background:var(--foot-dark);font-size:8.8px;color:#444;white-space:nowrap}
.bottom-bar nav{position:absolute;left:42px;top:15px}
.bottom-bar nav span{margin:0 5px;color:#777}
.bottom-bar .copy{position:absolute;right:30px;top:15px}
</style>
</head>
<body>
<div class="page">

<header class="site-header">
  <nav class="main-nav">
    <a class="active">Home</a><a>Who we are</a><a>How it works</a><a>Sign up</a><a>Login</a>
  </nav>
  <div class="brand"><span class="brand-mark"></span><span class="brand-name">Mira Lane</span></div>
  <div class="social-btn chirper"><i></i>Sign in with Chirper</div>
  <div class="social-btn friendbook"><i></i>Sign in with Friendbook</div>
  <div class="search">Search
    <svg width="9" height="9" viewBox="0 0 9 9"><circle cx="3.5" cy="3.5" r="2.6" fill="none" stroke="#9aa6aa" stroke-width="1.2"/><path d="M5.5 5.5 8.5 8.5" stroke="#9aa6aa" stroke-width="1.4"/></svg>
  </div>
</header>

<section class="category">
  <h1>Delivery</h1>
  <div class="more-cats">More Categories</div>
  <div class="rule"></div>
  <ul class="subnav">
    <li>Restaurant Delivery</li><li>Shipping</li><li>Nordhem Delivery</li><li>Courier</li><li>Bullseye Mart Delivery</li><li class="other">Other</li>
  </ul>
  <div class="post-task">POST A TASK</div>
</section>

<section class="recent">
  <h2>Recent Deliverys in All Cities</h2>
</section>

<svg width="0" height="0" style="position:absolute"><defs><path id="s" d="M5.5 0 7 3.8 11 4 7.9 6.6 9 10.8 5.5 8.5 2 10.8 3.1 6.6 0 4 4 3.8z"/></defs></svg>

<div class="abs" style="left:51px;top:262px;width:427px;height:680px">
  <article class="task" style="top:0">
    <div class="avatar" role="img" aria-label="Helper profile photo"></div><span class="level">Level - 15</span>
    <h3>Excepteur sint occaecat</h3>
    <p>At vero eos et accusamus et iusto odio dignissimos ducimus qui blanditiis praesentium voluptatum deleniti atque corrupti quos dolores et quas molestias excepturi sint occaecati cupiditate non provi dent similique sunt in culpa...</p>
    <div class="task-bar">Tasks of this type: <span class="price">$39 - $55</span>
      <span class="rating">Rating : <svg width="56" height="11" viewBox="0 0 56 11"><g fill="#3fb4c8"><use href="#s"/><use href="#s" x="11.3"/><use href="#s" x="22.6"/><use href="#s" x="33.9"/></g><use href="#s" x="45.2" fill="#a9b1b4"/></svg></span>
      <span class="use-template">USE TEMPLATE</span></div>
  </article>
  <article class="task" style="top:113px">
    <div class="avatar" role="img" aria-label="Helper profile photo"></div><span class="level">Level - 15</span>
    <h3>Excepteur sint occaecat</h3>
    <p>At vero eos et accusamus et iusto odio dignissimos ducimus qui blanditiis praesentium voluptatum deleniti atque corrupti quos dolores et quas molestias excepturi sint occaecati cupiditate non provi dent similique sunt in culpa...</p>
    <div class="task-bar">Tasks of this type: <span class="price">$39 - $55</span>
      <span class="rating">Rating : <svg width="56" height="11" viewBox="0 0 56 11"><g fill="#3fb4c8"><use href="#s"/><use href="#s" x="11.3"/><use href="#s" x="22.6"/><use href="#s" x="33.9"/></g><use href="#s" x="45.2" fill="#a9b1b4"/></svg></span>
      <span class="use-template">USE TEMPLATE</span></div>
  </article>
  <article class="task" style="top:226px">
    <div class="avatar" role="img" aria-label="Helper profile photo"></div><span class="level">Level - 15</span>
    <h3>Excepteur sint occaecat</h3>
    <p>At vero eos et accusamus et iusto odio dignissimos ducimus qui blanditiis praesentium voluptatum deleniti atque corrupti quos dolores et quas molestias excepturi sint occaecati cupiditate non provi dent similique sunt in culpa...</p>
    <div class="task-bar">Tasks of this type: <span class="price">$39 - $55</span>
      <span class="rating">Rating : <svg width="56" height="11" viewBox="0 0 56 11"><g fill="#3fb4c8"><use href="#s"/><use href="#s" x="11.3"/><use href="#s" x="22.6"/><use href="#s" x="33.9"/></g><use href="#s" x="45.2" fill="#a9b1b4"/></svg></span>
      <span class="use-template">USE TEMPLATE</span></div>
  </article>
  <article class="task" style="top:339px">
    <div class="avatar" role="img" aria-label="Helper profile photo"></div><span class="level">Level - 15</span>
    <h3>Excepteur sint occaecat</h3>
    <p>At vero eos et accusamus et iusto odio dignissimos ducimus qui blanditiis praesentium voluptatum deleniti atque corrupti quos dolores et quas molestias excepturi sint occaecati cupiditate non provi dent similique sunt in culpa...</p>
    <div class="task-bar">Tasks of this type: <span class="price">$39 - $55</span>
      <span class="rating">Rating : <svg width="56" height="11" viewBox="0 0 56 11"><g fill="#3fb4c8"><use href="#s"/><use href="#s" x="11.3"/><use href="#s" x="22.6"/><use href="#s" x="33.9"/></g><use href="#s" x="45.2" fill="#a9b1b4"/></svg></span>
      <span class="use-template">USE TEMPLATE</span></div>
  </article>
  <article class="task" style="top:452px">
    <div class="avatar" role="img" aria-label="Helper profile photo"></div><span class="level">Level - 15</span>
    <h3>Excepteur sint occaecat</h3>
    <p>At vero eos et accusamus et iusto odio dignissimos ducimus qui blanditiis praesentium voluptatum deleniti atque corrupti quos dolores et quas molestias excepturi sint occaecati cupiditate non provi dent similique sunt in culpa...</p>
    <div class="task-bar">Tasks of this type: <span class="price">$39 - $55</span>
      <span class="rating">Rating : <svg width="56" height="11" viewBox="0 0 56 11"><g fill="#3fb4c8"><use href="#s"/><use href="#s" x="11.3"/><use href="#s" x="22.6"/><use href="#s" x="33.9"/></g><use href="#s" x="45.2" fill="#a9b1b4"/></svg></span>
      <span class="use-template">USE TEMPLATE</span></div>
  </article>
  <article class="task" style="top:565px">
    <div class="avatar" role="img" aria-label="Helper profile photo"></div><span class="level">Level - 15</span>
    <h3>Excepteur sint occaecat</h3>
    <p>At vero eos et accusamus et iusto odio dignissimos ducimus qui blanditiis praesentium voluptatum deleniti atque corrupti quos dolores et quas molestias excepturi sint occaecati cupiditate non provi dent similique sunt in culpa...</p>
    <div class="task-bar">Tasks of this type: <span class="price">$39 - $55</span>
      <span class="rating">Rating : <svg width="56" height="11" viewBox="0 0 56 11"><g fill="#3fb4c8"><use href="#s"/><use href="#s" x="11.3"/><use href="#s" x="22.6"/><use href="#s" x="33.9"/></g><use href="#s" x="45.2" fill="#a9b1b4"/></svg></span>
      <span class="use-template">USE TEMPLATE</span></div>
  </article>
</div>

<div class="pager">
  <span>« Previous</span><span class="on">1</span><span>2</span><span>3</span><span>4</span><span>5</span><span>6</span><span>7</span><span>8</span><span>9</span><span>10</span><span class="gap">....</span><span>212</span><span>213</span><span class="next">Next »</span>
</div>

<aside class="widget price-widget">
  <h2>TaskPrice for Tasks of this type</h2>
  <p class="sub">Based on Historical Data</p>
  <div class="price-row" style="top:86px"><b>$10</b><span class="track"><i style="width:27%"></i></span></div>
  <div class="price-row" style="top:117px"><b>$30</b><span class="track"><i style="width:63%"></i></span></div>
  <div class="price-row" style="top:148px"><b>$45</b><span class="track"><i style="width:36%"></i></span></div>
  <div class="price-row" style="top:178px"><b>$60</b><span class="track"><i style="width:31%"></i></span></div>
  <div class="price-row" style="top:209px"><b>$80</b><span class="track"><i style="width:27%"></i></span></div>
  <div class="price-row" style="top:239px"><b>$95</b><span class="track"><i style="width:27%"></i></span></div>
</aside>

<aside class="widget city-widget">
  <h2>View Delivery Tasks by city</h2>
  <ul class="city-list">
    <li>All Cities</li><li>Chicago</li><li>Portland</li>
    <li>Austin</li><li>LA &amp; OC</li><li>SF Bay Area</li>
    <li>Boston</li><li>New York City</li><li>San Antonio</li>
  </ul>
  <div class="map" role="img" aria-label="Street map of the selected city with a location pin"></div>
</aside>

<section class="popular">
  <div class="popular-col" style="left:19px"><h3>Popular Cities in Australia</h3>
    <ul class="arrow-list"><li>Melbourne</li><li>Sydney</li><li>Adelaide</li><li>Berth</li></ul></div>
  <div class="popular-col" style="left:203px"><h3>Popular Cities in Singapore</h3>
    <ul class="arrow-list"><li>Aljunied</li><li>Bencoolen</li><li>Dunearn</li><li>Ayer Rajah</li></ul></div>
  <div class="popular-col" style="left:387px"><h3>Popular Cities in Malaysia</h3>
    <ul class="arrow-list"><li>George Town</li><li>Kuala Lumpur</li><li>Ipoh</li><li>Kuching</li></ul></div>
  <div class="popular-col" style="left:572px"><h3>Popular Cities in Philipines</h3>
    <ul class="arrow-list"><li>Abra</li><li>Agusan del Sur</li><li>Basilan</li><li>Cagayan</li></ul></div>
</section>

<footer class="site-footer">
  <div class="foot-col" style="left:41px"><h4>About us</h4>
    <ul class="arrow-list"><li>Praesent tempor</li><li>Cras vel</li><li>Etiam porttitor</li></ul></div>
  <div class="foot-col" style="left:149px;top:32px">
    <ul class="arrow-list"><li>Praesent tempor</li><li>Cras vel</li><li>Etiam porttitor</li></ul></div>
  <div class="foot-col" style="left:256px"><h4>Credit Details</h4>
    <ul class="arrow-list"><li>Praesent tempor</li><li>Cras vel</li><li>Etiam porttitor</li></ul></div>
  <div class="foot-col" style="left:364px"><h4>Popular Cities</h4>
    <ul class="arrow-list"><li>Praesent tempor</li><li>Cras vel</li><li>Etiam porttitor</li></ul></div>
  <div class="foot-col" style="left:471px"><h4>Customer Support</h4>
    <ul class="arrow-list"><li>Praesent tempor</li><li>Cras vel</li><li>Etiam porttitor</li></ul></div>
  <div class="foot-col" style="left:591px"><h4>Payments</h4>
    <div class="cards"><i></i><i></i><i></i><i></i><i></i></div>
    <p class="call">Call us : 555 010 2040</p></div>
</footer>

<div class="bottom-bar">
  <nav>Home<span>|</span>Who we are<span>|</span>How it works<span>|</span>Sign up<span>|</span>Log in<span>|</span>FAQ<span>|</span>Support<span>|</span>Privacy Policy<span>|</span>Terms and Conditions</nav>
  <p class="copy">Copyright © 2012 Mira Lane.&nbsp;&nbsp; All rights reserved.</p>
</div>

</div>
</body>
</html>
```